Computer Training in the Education sector - Letterhead

We need a new letter head to be designed for the company. We provide computer training fro the Education Sector, both primary and private tertiary providers. The colours will need to tie in with the website www.crossingthestream.co.nz.
The company name is Crossing the Stream with the tag line of Computer Training for Educators.
The footer will need to have the following detail...
0508 PCS MENTOR
021 839 415
www.crossingthestream.co.nz / training@crossingthestream.co.nz
Updates

Thanks for the designs so far.

Some have watermarks in the background. Please don't worry about using watermarks as I will not be using a watermark in in a final design.
Regards,
Roger

Thank you for all the designs and the effort. There was some great concepts that came through.

Cheers
Roger

Industry/Entity Type

Computer

```html
<!DOCTYPE html>
<html lang="en">
<head>
<meta charset="utf-8">
<title>Crossing the Stream – Letterhead</title>
<link rel="stylesheet" href="https://fonts.googleapis.com/css2?family=Arimo:wght@400;700&family=Didact+Gothic&display=swap">
<style>
  :root {
    --backdrop: #666666;
    --paper: #ffffff;
    --wave-blue: #6699ff;
    --wave-green: #22c21e;
    --wave-orange: #ff9900;
    --footer-violet: #6666ff;
    --name-blue: #5b8ee6;
    --ink: #222222;
    --rule: #111111;
  }
  * { box-sizing: border-box; margin: 0; padding: 0; }
  html, body {
    width: 1200px; height: 1000px; overflow: hidden;
    background: var(--backdrop);
  }
  .letterhead {
    position: absolute; left: 280px; top: 47px;
    width: 640px; height: 905px;
    background: var(--paper);
    box-shadow: 4px 6px 14px rgba(0,0,0,0.45);
    overflow: hidden;
  }
  .header-waves { position: absolute; left: 0; top: 0; width: 640px; height: 110px; display: block; }
  .brand {
    position: absolute; left: 28px; top: 108px;
    display: flex; align-items: center; gap: 16px;
  }
  .brand-mark {
    width: 62px; height: 62px; border-radius: 50%;
    background: var(--wave-green); flex: none;
  }
  .brand-name {
    font-family: "Arimo", Arial, sans-serif; font-weight: 700;
    font-size: 35px; color: var(--name-blue); letter-spacing: -0.3px;
    line-height: 1;
  }
  .brand-tagline {
    font-family: "Didact Gothic", sans-serif; font-size: 13px;
    color: var(--ink); text-align: right; margin-top: 4px;
  }
  .date-field {
    position: absolute; right: 32px; top: 172px;
    font-family: "Arimo", Arial, sans-serif; font-weight: 700; font-size: 13px;
    color: var(--ink); display: flex; align-items: flex-end; gap: 6px;
  }
  .date-line { width: 150px; border-bottom: 1px solid var(--rule); height: 12px; }
  .header-rule {
    position: absolute; left: 0; right: 0; top: 212px;
    border-top: 2px solid var(--rule);
  }
  .footer { position: absolute; left: 0; bottom: 0; width: 640px; height: 170px; }
  .footer-waves { position: absolute; inset: 0; width: 100%; height: 100%; display: block; }
  .footer-contacts {
    position: absolute; left: 48px; bottom: 18px;
    font-family: "Didact Gothic", sans-serif; font-size: 13px; color: #fff;
    display: grid; grid-template-columns: 60px auto; row-gap: 8px;
  }
  .footer-phone {
    position: absolute; right: 40px; bottom: 66px;
    display: flex; align-items: center; gap: 14px;
    font-family: "Didact Gothic", sans-serif; font-size: 13px; color: #fff;
    line-height: 1.7;
  }
  .phone-icon { width: 24px; height: 20px; flex: none; }
</style>
</head>
<body>
  <main class="letterhead">
    <svg class="header-waves" viewBox="0 0 640 110" preserveAspectRatio="none" aria-hidden="true">
      <path d="M0,0 H640 V40 C470,62 250,80 0,108 Z" fill="var(--wave-orange)"/>
      <path d="M0,0 H640 V30 C470,50 250,62 0,88 Z" fill="var(--wave-green)"/>
      <path d="M0,0 H640 V20 C470,36 250,44 0,66 Z" fill="var(--wave-blue)"/>
    </svg>

    <header class="brand">
      <span class="brand-mark" aria-hidden="true"></span>
      <div>
        <div class="brand-name">Crossing the Stream</div>
        <div class="brand-tagline">… Computer Training for Educators</div>
      </div>
    </header>

    <div class="date-field"><span>Date:</span><span class="date-line"></span></div>
    <div class="header-rule"></div>

    <footer class="footer">
      <svg class="footer-waves" viewBox="0 0 640 170" preserveAspectRatio="none" aria-hidden="true">
        <path d="M0,170 V76 C220,72 430,66 640,0 V170 Z" fill="var(--wave-orange)"/>
        <path d="M0,170 V82 C220,79 440,72 640,24 V170 Z" fill="var(--wave-green)"/>
        <path d="M0,170 V90 C220,88 450,80 640,50 V170 Z" fill="var(--footer-violet)"/>
      </svg>
      <div class="footer-contacts">
        <span>Email:</span><span>training@crossingthestream.co.nz</span>
        <span>Website:</span><span>www.crossingthestream.co.nz</span>
      </div>
      <div class="footer-phone">
        <svg class="phone-icon" viewBox="0 0 24 20" aria-hidden="true">
          <path d="M2,6 C2,2 22,2 22,6 L22,8 L17,8 L17,5.5 C14,4.6 10,4.6 7,5.5 L7,8 L2,8 Z" fill="#fff"/>
          <path d="M6,9 L18,9 L21,18 L3,18 Z" fill="#fff"/>
          <circle cx="12" cy="13.5" r="2.4" fill="var(--footer-violet)"/>
        </svg>
        <div>021 839 415 or<br>0508 PCS MENTOR</div>
      </div>
    </footer>
  </main>
</body>
</html>
```